Banner ad series

We need a series of banner ads for 4 different digital products. The ads will drive traffic to these landing pages:
Relocate.set: http://pinnedtidygoods.example/relocatekit/
Treasures.file: http://pinnedtidygoods.example/digital-treasures-file/
Jumpstart Drill School: http://pinnedtidygoods.example/jumpstart-drill-school/
Vital Habits Drill School: http://pinnedtidygoods.example/vital-habits/

Banner Ad Sizes needed:
160x600, 728x90, 300x250

Text files with the copy/variations needed for each product are attached. In the text file - the first line of each option is the main headline. All other copy is support copy and OPTIONAL.

Target Market(s)

Our target market is a woman between the ages of 30-55 with kids. She's smart, working professionally and always on the lookout for products and services that will help her get more organized.

Industry/Entity Type

Digital

Requirements
Must have
• Pinned Tidy logo

```html
<!DOCTYPE html>
<html lang="en">
<head>
<meta charset="utf-8">
<title>Pinned Tidy – Jumpstart Drill School banner set</title>
<link rel="stylesheet" href="https://fonts.googleapis.com/css2?family=Asap+Condensed:wght@400;600;700&display=swap">
<style>
  :root {
    --backdrop: #4b2e1f;
    --green: #3a9414;
    --green-dark: #2a7a0c;
    --green-light: #7cc242;
    --white: #ffffff;
    --brand-ink: #2a7a0c;
    --orange: #f57d16;
    --orange-light: #ffb25a;
    --button-ink: #ffffff;
    --arrow-bg: #1f1f1f;
    --photo-a: #f2f1ec;
    --photo-b: #d9dcd6;
  }
  * { margin: 0; padding: 0; box-sizing: border-box; }
  html, body { width: 1200px; height: 763px; overflow: hidden; background: var(--backdrop); }
  body { font-family: "Asap Condensed", "Arial Narrow", sans-serif; }

  .stage {
    position: relative; width: 1040px; height: 661px;
    transform: scale(1.1538); transform-origin: 0 0;
  }
  .banner { position: absolute; overflow: hidden; background: var(--green); color: var(--white); }

  .photo {
    position: absolute;
    background: linear-gradient(160deg, var(--photo-a) 0%, var(--photo-b) 60%, #c9cfc4 100%);
  }
  .curve { position: absolute; display: block; }

  .brand {
    position: absolute; inset: 0;
    display: flex; align-items: center; justify-content: center; gap: 6px;
  }
  .brand-mark { width: 8px; height: 8px; background: var(--brand-ink); }
  .brand-name { color: var(--brand-ink); font-weight: 600; font-size: 18px; line-height: 1; }

  .headline { font-weight: 700; text-transform: uppercase; line-height: 1.05; text-align: center; }
  .support { font-weight: 400; line-height: 1.2; text-align: center; }
  .rule { border: 0; border-top: 1px dotted rgba(255,255,255,.7); }

  .cta {
    position: absolute; display: flex; align-items: center; justify-content: center; gap: 8px;
    border-radius: 16px; border: 2px solid #fff2e2;
    background: linear-gradient(180deg, var(--orange-light) 0%, var(--orange) 55%, #e0650a 100%);
    color: var(--button-ink); font-weight: 700; font-size: 15px;
    box-shadow: 0 2px 3px rgba(0,0,0,.3);
  }
  .cta-arrow { width: 22px; height: 22px; border-radius: 50%; background: var(--arrow-bg); display: flex; align-items: center; justify-content: center; }

  /* skyscraper 160x600 */
  .sky { left: 70px; top: 25px; width: 160px; height: 600px; }
  .sky .top { position: absolute; left: 0; top: 0; width: 160px; height: 78px; background: var(--white); }
  .sky .photo { left: 0; top: 78px; width: 160px; height: 252px; }
  .sky .copy { position: absolute; left: 4px; right: 4px; top: 338px; }
  .sky .h1 { font-size: 20px; }
  .sky .h2 { font-size: 18px; margin-top: 18px; }
  .sky .rule { margin: 6px 16px; }
  .sky .support { font-size: 13.5px; margin-top: 10px; }
  .sky .cta { left: 6px; top: 553px; width: 150px; height: 34px; }

  /* medium rectangle 300x250 */
  .rect { top: 75px; width: 300px; height: 250px; }
  .rect-a { left: 321px; } .rect-b { left: 642px; }
  .rect .top { position: absolute; left: 0; top: 0; width: 156px; height: 72px; background: var(--white); }
  .rect .photo { left: 150px; top: 0; width: 150px; height: 250px; }
  .rect .copy { position: absolute; left: 2px; width: 146px; top: 81px; }
  .rect .h1 { font-size: 20px; }
  .rect .h2 { font-size: 17px; margin-top: 7px; }
  .rect .rule { margin: 3px 12px; }
  .rect .support { font-size: 13px; margin-top: 5px; }
  .rect .cta { left: 152px; top: 205px; width: 144px; height: 32px; }

  /* leaderboard 728x90 */
  .board { left: 257px; width: 728px; height: 90px; }
  .board-a { top: 359px; } .board-b { top: 461px; }
  .board .top { position: absolute; left: 0; top: 0; width: 153px; height: 90px; background: var(--white); }
  .board .photo { left: 485px; top: 0; width: 243px; height: 90px; }
  .board .copy { position: absolute; left: 156px; width: 318px; top: 5px; }
  .board .h1 { font-size: 22px; line-height: 1.08; }
  .board .support { font-size: 13px; margin-top: 2px; line-height: 1.15; }
  .board .cta { left: 556px; top: 35px; width: 148px; height: 32px; }
</style>
</head>
<body>
<main class="stage">

  <section class="banner sky" aria-label="160 by 600 banner">
    <div class="top"><div class="brand"><span class="brand-mark"></span><span class="brand-name">Pinned Tidy</span></div></div>
    <div class="photo" role="img" aria-label="Tidy white wall organizer with memo board, pockets and hooks"></div>
    <svg class="curve" style="left:0;top:300px" width="160" height="44" viewBox="0 0 160 44">
      <path d="M0 30 Q80 0 160 12 L160 44 L0 44 Z" fill="var(--green-light)"/>
      <path d="M0 36 Q80 8 160 20 L160 44 L0 44 Z" fill="var(--green)"/>
    </svg>
    <div class="copy">
      <p class="headline h1">Now that it's<br>the new year</p>
      <hr class="rule">
      <p class="headline h2">It's time to<br>get organized!</p>
      <hr class="rule">
      <p class="support">Sign Up for the Jumpstart Drill School &amp; Organize your home AND your life</p>
    </div>
    <a class="cta">Learn More! <span class="cta-arrow"><svg width="10" height="10" viewBox="0 0 10 10"><path d="M3 1 L7 5 L3 9" stroke="#fff" stroke-width="2" fill="none"/></svg></span></a>
  </section>

  <section class="banner rect rect-a" aria-label="300 by 250 banner">
    <div class="photo" role="img" aria-label="Tidy white wall organizer with memo board, pockets and hooks"></div>
    <svg class="curve" style="left:120px;top:0" width="70" height="250" viewBox="0 0 70 250">
      <path d="M0 0 L56 0 Q20 80 34 250 L0 250 Z" fill="var(--green)"/>
      <path d="M56 0 L62 0 Q26 80 40 250 L34 250 Q20 80 56 0 Z" fill="var(--green-light)"/>
    </svg>
    <div class="top"><div class="brand"><span class="brand-mark"></span><span class="brand-name">Pinned Tidy</span></div></div>
    <div class="copy">
      <p class="headline h1">Now that it's<br>the new year</p>
      <hr class="rule">
      <p class="headline h2">It's time to<br>get organized!</p>
      <hr class="rule">
      <p class="support">Sign Up for the Jumpstart Drill School &amp; Organize your home AND your life</p>
    </div>
    <a class="cta">Learn More! <span class="cta-arrow"><svg width="10" height="10" viewBox="0 0 10 10"><path d="M3 1 L7 5 L3 9" stroke="#fff" stroke-width="2" fill="none"/></svg></span></a>
  </section>

  <section class="banner rect rect-b" aria-label="300 by 250 banner">
    <div class="photo" role="img" aria-label="Tidy white wall organizer with memo board, pockets and hooks"></div>
    <svg class="curve" style="left:120px;top:0" width="70" height="250" viewBox="0 0 70 250">
      <path d="M0 0 L56 0 Q20 80 34 250 L0 250 Z" fill="var(--green)"/>
      <path d="M56 0 L62 0 Q26 80 40 250 L34 250 Q20 80 56 0 Z" fill="var(--green-light)"/>
    </svg>
    <div class="top"><div class="brand"><span class="brand-mark"></span><span class="brand-name">Pinned Tidy</span></div></div>
    <div class="copy">
      <p class="headline h1">Now that it's<br>the new year</p>
      <hr class="rule">
      <p class="headline h2">It's time to<br>get organized!</p>
      <hr class="rule">
      <p class="support">Sign Up for the Jumpstart Drill School &amp; Organize your home AND your life</p>
    </div>
    <a class="cta">Learn More! <span class="cta-arrow"><svg width="10" height="10" viewBox="0 0 10 10"><path d="M3 1 L7 5 L3 9" stroke="#fff" stroke-width="2" fill="none"/></svg></span></a>
  </section>

  <section class="banner board board-a" aria-label="728 by 90 banner">
    <div class="top"><div class="brand"><span class="brand-mark"></span><span class="brand-name">Pinned Tidy</span></div></div>
    <div class="photo" role="img" aria-label="Tidy white wall organizer with pockets and hooks"></div>
    <svg class="curve" style="left:470px;top:0" width="40" height="90" viewBox="0 0 40 90">
      <path d="M0 0 L34 0 Q12 40 20 90 L0 90 Z" fill="var(--green)"/>
      <path d="M34 0 L38 0 Q16 40 24 90 L20 90 Q12 40 34 0 Z" fill="var(--green-light)"/>
    </svg>
    <div class="copy">
      <p class="headline h1">Now that it's the new year<br>it's time to get organized!</p>
      <p class="support">Sign Up for the Jumpstart Drill School &amp; Organize your home AND your life</p>
    </div>
    <a class="cta">Learn More! <span class="cta-arrow"><svg width="10" height="10" viewBox="0 0 10 10"><path d="M3 1 L7 5 L3 9" stroke="#fff" stroke-width="2" fill="none"/></svg></span></a>
  </section>

  <section class="banner board board-b" aria-label="728 by 90 banner">
    <div class="top"><div class="brand"><span class="brand-mark"></span><span class="brand-name">Pinned Tidy</span></div></div>
    <div class="photo" role="img" aria-label="Tidy white wall organizer with pockets and hooks"></div>
    <svg class="curve" style="left:470px;top:0" width="40" height="90" viewBox="0 0 40 90">
      <path d="M0 0 L34 0 Q12 40 20 90 L0 90 Z" fill="var(--green)"/>
      <path d="M34 0 L38 0 Q16 40 24 90 L20 90 Q12 40 34 0 Z" fill="var(--green-light)"/>
    </svg>
    <div class="copy">
      <p class="headline h1">Now that it's the new year<br>it's time to get organized!</p>
      <p class="support">Sign Up for the Jumpstart Drill School &amp; Organize your home AND your life</p>
    </div>
    <a class="cta">Learn More! <span class="cta-arrow"><svg width="10" height="10" viewBox="0 0 10 10"><path d="M3 1 L7 5 L3 9" stroke="#fff" stroke-width="2" fill="none"/></svg></span></a>
  </section>

</main>
</body>
</html>
```